Velk Partners Building Business Cards

We need a business card that reflects our business as "Solar Experts" in San Diego. Browse our website www.velkpartners.example our License needs to be displayed as "CSLB# 3867140" our phone number is (619) 555-0187

Save thousands on your electric bills and increase the value of your home while helping to protect the environment. Our solar installation experts will help you design the system that's right for you, using only the highest quality equipment that will look great and give you ideal performance. Our goal is to make you energy independent, and get your electric bill to 0.

Paul Osterby
(619) 555-0187
paul@velkpartners.example

Target Market(s)

Home owners in san diego looking for solar

Industry/Entity Type

Solar Energy

Contact Information for Business Card

Paul Osterby
(619) 555-0187
paul@velkpartners.example

Font styles to use
Other font styles liked:
• Use our logo font

Requirements
Must have
• License needs to be displayed as "CSLB# 3867140" our phone number is (619) 555-0187
Nice to have
• Real images of rooftop home solar in san diego
Should not have
• our business address

```html
<!DOCTYPE html>
<html lang="en">
<head>
<meta charset="utf-8">
<title>Velk Partners Building – Business Card</title>
<link rel="stylesheet" href="https://fonts.googleapis.com/css2?family=Roboto:wght@400;700&display=swap">
<style>
  :root {
    --brand-blue: #1a3d78;
    --brand-yellow: #f5ab00;
    --sun-pale: #fbe9c4;
    --wave-pale: #d3dbe8;
    --card-white: #ffffff;
    --text-grey: #555a60;
    --backdrop: #262626;
  }
  * { margin: 0; padding: 0; box-sizing: border-box; }
  html, body {
    width: 1200px;
    height: 987px;
    overflow: hidden;
    background: var(--backdrop);
    font-family: "Roboto", Arial, sans-serif;
  }
  .card {
    position: absolute;
    left: 293px;
    width: 615px;
    height: 350px;
    overflow: hidden;
  }
  .card-front { top: 131px; background: var(--card-white); }
  .card-back { top: 506px; background: var(--brand-blue); }

  .front-header { position: absolute; left: 0; top: 0; width: 615px; height: 350px; }

  .sun-decoration {
    position: absolute;
    right: 0;
    bottom: 0;
    width: 300px;
    height: 215px;
    background:
      radial-gradient(ellipse 70% 55% at 62% 62%, var(--sun-pale) 0%, rgba(251,233,196,0.6) 45%, rgba(255,255,255,0) 75%),
      linear-gradient(to top, var(--wave-pale) 0%, rgba(211,219,232,0) 35%);
  }

  .holder { position: absolute; right: 41px; top: 27px; text-align: right; color: var(--card-white); }
  .holder-name { font-size: 20px; font-weight: 700; letter-spacing: 0.3px; }
  .holder-title { font-size: 16px; font-weight: 400; margin-top: 6px; }

  .company-name {
    position: absolute;
    left: 41px;
    top: 136px;
    font-size: 30px;
    font-weight: 700;
    color: var(--brand-blue);
    letter-spacing: -0.5px;
    white-space: nowrap;
  }

  .license { position: absolute; left: 41px; top: 218px; font-size: 15px; color: var(--text-grey); }

  .contact-list { position: absolute; left: 41px; top: 251px; list-style: none; }
  .contact-item {
    display: flex;
    align-items: center;
    height: 23.5px;
    font-size: 15px;
    color: var(--text-grey);
  }
  .contact-icon { width: 16px; height: 16px; margin-right: 7px; fill: var(--brand-blue); flex: none; }

  .back-name {
    position: absolute;
    left: 0;
    right: 0;
    top: 140px;
    text-align: center;
    font-size: 38px;
    font-weight: 700;
    color: var(--card-white);
    letter-spacing: -0.5px;
  }
  .back-web {
    position: absolute;
    left: 0;
    right: 0;
    top: 292px;
    text-align: center;
    font-size: 13px;
    color: var(--card-white);
    letter-spacing: 5px;
  }
</style>
</head>
<body>

<section class="card card-front">
  <svg class="front-header" viewBox="0 0 525 298" aria-hidden="true">
    <path fill="var(--brand-yellow)" d="M0 0 H525 V101 C430 123 300 99 200 60 C140 35 85 23 45 68 C25 90 8 108 0 118 Z"/>
    <path fill="var(--brand-blue)" stroke="var(--card-white)" stroke-width="2" d="M0 -2 H527 V94 C430 114 300 90 200 51 C140 26 85 14 42 58 C22 80 6 99 0 108 Z"/>
  </svg>

  <div class="sun-decoration" role="img" aria-label="Faint sun and waves decoration"></div>

  <div class="holder">
    <div class="holder-name">Paul Osterby</div>
    <div class="holder-title">CEO/Founder</div>
  </div>

  <div class="company-name">Velk Partners Building</div>

  <p class="license">CSLB# 3867140</p>

  <ul class="contact-list">
    <li class="contact-item">
      <svg class="contact-icon" viewBox="0 0 16 16" aria-hidden="true"><path d="M2 5 C2 2.5 14 2.5 14 5 V6.5 H11 V5.5 H5 V6.5 H2 Z M4 8 H12 L13 14 H3 Z M8 9.2 A1.8 1.8 0 1 0 8.01 9.2 Z"/></svg>
      (619) 555-0187
    </li>
    <li class="contact-item">
      <svg class="contact-icon" viewBox="0 0 16 16" aria-hidden="true"><path d="M1 3.5 H15 V4.5 L8 9 L1 4.5 Z M1 6 L8 10.5 L15 6 V12.5 H1 Z"/></svg>
      paul@velkpartners.example
    </li>
    <li class="contact-item">
      <svg class="contact-icon" viewBox="0 0 16 16" aria-hidden="true"><circle cx="8" cy="8" r="7"/><path fill="var(--card-white)" d="M5 4 C7 4 7.5 6 6 7 C5 8 6 9.5 4 10 C3 8 3 5.5 5 4 Z M10 9 C11.5 9 12 11 10.5 12.5 C9.5 11.5 9 10 10 9 Z"/></svg>
      www.velkpartners.example
    </li>
  </ul>
</section>

<section class="card card-back">
  <div class="back-name">Velk Partners Building</div>
  <div class="back-web">www.velkpartners.example</div>
</section>

</body>
</html>
```